Stylish new business card needed!

Hello everyone! I am in need of a new business card design for an alarm company here in Hurricane WV. I have all fonts, color codes and logos provided for you use! We are a young company and like the style of a clean sleek looking business card. Would like it double sided, one side holding the logo and the other with your design!
Target Market(s)
The people that are looking for the newest tech for home automation and security
Industry/Entity Type
Alarm services; Home automation
Contact Information for Business Card
Name of person; position (Sales; Installer); Phone Number (555.418.7260); Employee cell Number; Website (www.GuardedByVelk.example); Employee Email; Double sided
Look and feel
Each slider illustrates characteristics of the customer's brand and the style your logo design should communicate.

```html
<!DOCTYPE html>
<html lang="en">
<head>
<meta charset="utf-8">
<title>Velk Business Card</title>
<link rel="stylesheet" href="https://fonts.googleapis.com/css2?family=Fira+Sans:wght@400;500&display=swap">
<style>
  :root {
    --page-bg: #2a2a2c;
    --brand-orange: #e2773a;
    --brand-orange-deep: #d2692f;
    --card-white: #f3f2f4;
    --ink-gray: #4a4a4c;
    --logo-white: #f1eef2;
  }
  html, body {
    margin: 0;
    width: 1200px;
    height: 1172px;
    overflow: hidden;
    background: var(--page-bg);
    font-family: "Fira Sans", Arial, sans-serif;
  }
  .card {
    position: absolute;
    left: 180px;
    width: 840px;
    height: 480px;
    box-sizing: border-box;
    box-shadow: 0 10px 30px rgba(0,0,0,.35);
  }
  .card-front {
    top: 90px;
    background: linear-gradient(160deg, var(--brand-orange), var(--brand-orange-deep));
    display: flex;
    align-items: center;
    justify-content: center;
  }
  .card-back {
    top: 610px;
    background: var(--card-white);
  }
  .brand-name {
    font-weight: 500;
    letter-spacing: 4px;
    line-height: 1;
    margin: 0;
  }
  .card-front .brand-name {
    color: var(--logo-white);
    font-size: 120px;
  }
  .card-back .brand-name {
    position: absolute;
    top: 56px;
    right: 64px;
    color: var(--brand-orange);
    font-size: 72px;
  }
  .contact {
    position: absolute;
    left: 64px;
    bottom: 52px;
    color: var(--ink-gray);
  }
  .contact-name {
    color: var(--brand-orange);
    font-size: 34px;
    font-weight: 500;
    margin: 0;
  }
  .contact-role {
    font-size: 20px;
    margin: 2px 0 14px;
  }
  .contact-list {
    list-style: none;
    margin: 0;
    padding: 0;
    font-size: 20px;
    line-height: 30px;
  }
  .contact-list li {
    display: flex;
    align-items: center;
    gap: 10px;
  }
  .contact-list svg {
    width: 16px;
    height: 16px;
    fill: var(--brand-orange);
    flex: none;
  }
</style>
</head>
<body>
  <section class="card card-front">
    <p class="brand-name">VELK</p>
  </section>

  <section class="card card-back">
    <p class="brand-name">VELK</p>
    <div class="contact">
      <p class="contact-name">Dan Harlow</p>
      <p class="contact-role">Manager</p>
      <ul class="contact-list">
        <li><svg viewBox="0 0 16 16" aria-hidden="true"><path d="M4 0h8a1 1 0 0 1 1 1v14a1 1 0 0 1-1 1H4a1 1 0 0 1-1-1V1a1 1 0 0 1 1-1zm1 2v10h6V2zm3 11a1 1 0 1 0 0 2 1 1 0 0 0 0-2z"/></svg>000-000-0000</li>
        <li><svg viewBox="0 0 16 16" aria-hidden="true"><path d="M3.6 1l2.6 3-1.5 1.8c.9 2 2.5 3.6 4.5 4.5L11 8.8l3 2.6-1.4 2.9C7 14 2 9 1.7 3.4z"/></svg>555-418-7260</li>
        <li><svg viewBox="0 0 16 16" aria-hidden="true"><path d="M1 3h14v10H1zm1.5 1.2V5l5.5 4 5.5-4v-.8z"/></svg>mail@GuardedByVelk.example</li>
        <li><svg viewBox="0 0 16 16" aria-hidden="true"><circle cx="8" cy="8" r="7"/></svg>www.GuardedByVelk.example</li>
      </ul>
    </div>
  </section>
</body>
</html>
```